Harborline Auto LLC

Car Dealer Customer Service
Address: 2874 Cresthaven Road, Shelbyville, TN 37162
web: www.harborlineautoxq.net
email: harborlineautoxq@mailnest.example
Phone: (931) 555-0148
Phone: (629) 555-0173

```html
<!DOCTYPE html>
<html lang="en">
<head>
<meta charset="utf-8">
<title>Harborline Auto LLC – Business Card</title>
<link rel="stylesheet" href="https://fonts.googleapis.com/css2?family=Montserrat:wght@700;800&family=Roboto:wght@400;500&display=swap">
<style>
  :root {
    --backdrop: #3a3a3a;
    --card: #1b1b1c;
    --edge-blue: #2a8fd0;
    --brand-blue: #2a8fd0;
    --accent-gold: #f0b23c;
    --text-light: #f1f1f1;
    --emboss-grey: #6a6a6c;
  }
  * { margin: 0; padding: 0; box-sizing: border-box; }
  html, body { width: 1200px; height: 801px; overflow: hidden; }
  body {
    background: var(--backdrop);
    display: flex;
    align-items: center;
    justify-content: center;
    gap: 44px;
    font-family: "Roboto", Arial, sans-serif;
  }
  .card {
    position: relative;
    width: 540px;
    height: 309px;
    background: var(--card);
    border-bottom: 3px solid var(--edge-blue);
    border-left: 2px solid var(--edge-blue);
    box-shadow: 0 18px 36px rgba(0,0,0,.45);
    overflow: hidden;
  }
  /* Front */
  .contact {
    position: absolute;
    left: 46px;
    bottom: 52px;
    color: var(--text-light);
    font-size: 13.5px;
    line-height: 1.38;
  }
  .contact .role {
    color: var(--brand-blue);
    font-weight: 500;
    font-size: 14.5px;
  }
  .contact .address { margin-bottom: 10px; }
  .contact-row { display: flex; align-items: center; gap: 8px; }
  .contact-row svg { width: 12px; height: 12px; flex: none; }
  .brand-front {
    position: absolute;
    right: 44px;
    top: 70px;
    display: flex;
    flex-direction: column;
    align-items: center;
    gap: 14px;
  }
  .brand-mark {
    width: 62px;
    height: 62px;
    border-radius: 50%;
    background: var(--brand-blue);
  }
  .brand-name {
    font-family: "Montserrat", Arial, sans-serif;
    font-weight: 800;
    font-size: 24px;
    letter-spacing: 1px;
    color: var(--brand-blue);
    text-transform: uppercase;
  }
  /* Back */
  .card-back {
    display: flex;
    flex-direction: column;
    align-items: center;
    justify-content: center;
    gap: 18px;
  }
  .card-back .brand-mark { width: 96px; height: 96px; background: var(--emboss-grey); }
  .card-back .brand-name { font-size: 32px; color: var(--emboss-grey); }
</style>
</head>
<body>
  <section class="card card-front">
    <div class="brand-front">
      <div class="brand-mark"></div>
      <div class="brand-name">Harborline Auto</div>
    </div>
    <div class="contact">
      <p class="role">Car Dealer Customer Service</p>
      <p class="address">2874 Cresthaven Road<br>Shelbyville, TN 37162</p>
      <p class="contact-row">
        <svg viewBox="0 0 12 12"><path d="M2.5 1 L4.5 1 L5.2 3.6 L4 4.6 C4.6 6 6 7.4 7.4 8 L8.4 6.8 L11 7.5 L11 9.5 C11 10.4 10.4 11 9.5 11 C5 11 1 7 1 2.5 C1 1.6 1.6 1 2.5 1 Z" fill="var(--accent-gold)"/></svg>
        (931) 555-0148
      </p>
      <p class="contact-row">
        <svg viewBox="0 0 12 12"><path d="M2.5 1 L4.5 1 L5.2 3.6 L4 4.6 C4.6 6 6 7.4 7.4 8 L8.4 6.8 L11 7.5 L11 9.5 C11 10.4 10.4 11 9.5 11 C5 11 1 7 1 2.5 C1 1.6 1.6 1 2.5 1 Z" fill="var(--accent-gold)"/></svg>
        (629) 555-0173
      </p>
      <p class="contact-row">
        <svg viewBox="0 0 12 12"><rect x="1" y="2.5" width="10" height="7" rx="1" fill="var(--accent-gold)"/><path d="M1.5 3 L6 6.5 L10.5 3" stroke="var(--card)" stroke-width="1" fill="none"/></svg>
        harborlineautoxq@mailnest.example
      </p>
      <p class="contact-row">
        <svg viewBox="0 0 12 12"><circle cx="6" cy="6" r="5" fill="var(--accent-gold)"/><path d="M1 6 H11 M6 1 C3.5 3.5 3.5 8.5 6 11 M6 1 C8.5 3.5 8.5 8.5 6 11" stroke="var(--card)" stroke-width=".8" fill="none"/></svg>
        www.harborlineautoxq.net
      </p>
    </div>
  </section>

  <section class="card card-back">
    <div class="brand-mark"></div>
    <div class="brand-name">Harborline Auto</div>
  </section>
</body>
</html>
```